A3 Poster & DL Flyer Design Project

We need a poster and flyer designed to advertise a Wine, Food and Live music event.
Event title is "A Sip of Fine Moments" and is put on by Harlow's Creek Wines. Date for the event is Sunday 21 April 2013
The outdoor event covers wine, gourmet food and live music
Live music genera is Jazz, Blues, Swing
Updates

Project Deadline Extended
Reason: Most of the designs did not meet our requirements only 3 out of 21 have potential but would like to see more

Target Market(s)

25 - 55 wine drinkers with money.

Industry/Entity Type

Event

Requirements
Must have
• Title of the Event "A Sip of Fine Moments"
Date Sunday 21 April 2013 or be generic where we can write the date on each year.
Heron Logo
Entry is Free
No BYO Alcohol
Must reflect Wine, Food & Live Music

```html
<!DOCTYPE html>
<html lang="en">
<head>
<meta charset="utf-8">
<title>A Sip of Fine Moments – Harlow's Creek Wines</title>
<link href="https://fonts.googleapis.com/css2?family=Roboto:wght@300;400&family=Roboto+Condensed:wght@700&family=Libre+Baskerville:wght@400;700&display=swap" rel="stylesheet">
<style>
  :root {
    --backdrop: #efeeec;
    --wood-dark: #3a1810;
    --wood-mid: #6b2e1c;
    --wood-light: #8a3f26;
    --band: #e6d3cc;
    --band-text: #3a2a24;
    --cream: #fbf4ec;
    --plank: #cfa77a;
    --plank-edge: #9c744c;
    --plank-text: #2a1408;
    --rope: #b89a72;
    --badge-red: #a3161e;
    --badge-ring: #e9e4e2;
  }
  * { box-sizing: border-box; margin: 0; padding: 0; }
  html, body { width: 1200px; height: 882px; overflow: hidden; background: var(--backdrop); }
  .poster {
    position: absolute; left: 335px; top: 31px; width: 530px; height: 820px; overflow: hidden;
    background:
      linear-gradient(180deg, rgba(0,0,0,0.15) 0%, rgba(0,0,0,0) 40%, rgba(0,0,0,0.35) 100%),
      linear-gradient(90deg, var(--wood-dark) 0%, var(--wood-mid) 35%, var(--wood-light) 60%, var(--wood-mid) 80%, var(--wood-dark) 100%);
    box-shadow: 0 6px 18px rgba(0,0,0,0.25);
    font-family: "Roboto", Arial, sans-serif;
  }
  .brand-mark {
    position: absolute; left: 14px; top: 44px; display: flex; align-items: center; gap: 8px;
    font-family: "Libre Baskerville", Georgia, serif; font-size: 13px; color: var(--band);
  }
  .brand-mark .dot { width: 14px; height: 14px; border-radius: 50%; background: var(--band); }
  .brand-band {
    position: absolute; left: 0; top: 90px; width: 100%; height: 30px; background: var(--band); opacity: 0.88;
    display: flex; align-items: center; justify-content: flex-end; padding-right: 8px;
    font-family: "Libre Baskerville", Georgia, serif; font-size: 14px; letter-spacing: 0.6px; color: var(--band-text);
  }
  .title { position: absolute; left: 0; top: 136px; width: 100%; text-align: center; color: var(--cream); text-shadow: 0 2px 4px rgba(0,0,0,0.45); }
  .title .line { display: block; font-weight: 300; line-height: 1.05; }
  .title .line-1 { font-size: 50px; }
  .title .line-2 { font-size: 46px; margin-top: 6px; }
  .title .strong { font-weight: 400; font-size: 1.2em; }
  .title .byline { display: block; font-size: 27px; font-weight: 400; margin-top: 6px; }
  .divider { position: absolute; left: 0; top: 330px; width: 100%; height: 4px; background: rgba(20,6,2,0.55); }
  .highlights { position: absolute; left: 0; top: 334px; width: 300px; height: 330px; }
  .rope { position: absolute; top: 0; width: 2px; height: 300px; background: var(--rope); }
  .rope.left { left: 50px; } .rope.right { left: 258px; }
  .plank {
    position: absolute; left: 28px; width: 258px; height: 46px; border-radius: 4px;
    background: linear-gradient(180deg, var(--plank) 0%, #d9b68c 45%, var(--plank-edge) 100%);
    box-shadow: 0 3px 5px rgba(0,0,0,0.45);
    display: flex; align-items: center; justify-content: center;
    font-family: "Roboto Condensed", "Arial Narrow", sans-serif; font-weight: 700; font-size: 28px; color: var(--plank-text);
  }
  .date-badge {
    position: absolute; left: 93px; top: 658px; width: 124px; height: 124px; border-radius: 50%;
    background: radial-gradient(circle at 50% 35%, #c3242c 0%, var(--badge-red) 60%, #7c0e14 100%);
    border: 6px solid var(--badge-ring); box-shadow: 0 3px 6px rgba(0,0,0,0.4);
    display: flex; flex-direction: column; align-items: center; justify-content: center;
    font-family: "Libre Baskerville", Georgia, serif; font-weight: 700; color: #fff; font-size: 22px; line-height: 1.2;
  }
  .date-badge sup { font-size: 12px; }
  .still-life {
    position: absolute; left: 287px; top: 373px; width: 243px; height: 447px;
    background:
      radial-gradient(ellipse at 55% 85%, #a9ad4c 0%, #7f8a35 30%, rgba(90,60,20,0) 60%),
      radial-gradient(ellipse at 60% 30%, #3d4a1c 0%, rgba(40,30,10,0) 55%),
      linear-gradient(180deg, #6a1e14 0%, #4a140d 60%, #2c0c07 100%);
  }
</style>
</head>
<body>
  <main class="poster">
    <div class="brand-mark"><span class="dot"></span>Harlow's Creek Wines</div>
    <div class="brand-band">HARLOW'S CREEK WINES</div>
    <h1 class="title">
      <span class="line line-1">A <span class="strong">Sip</span></span>
      <span class="line line-2">of <span class="strong">Fine</span> Moments</span>
      <span class="byline">by Harlow's Creek Wines</span>
    </h1>
    <div class="divider"></div>
    <ul class="highlights">
      <li class="rope left"></li>
      <li class="rope right"></li>
      <li class="plank" style="top:22px">Wine</li>
      <li class="plank" style="top:81px">Gourmet Food</li>
      <li class="plank" style="top:139px">Live Music</li>
      <li class="plank" style="top:196px">Entry is Free</li>
      <li class="plank" style="top:252px">No BYO Alcohol</li>
    </ul>
    <div class="date-badge"><span>21<sup>st</sup></span><span>APRIL</span><span>2013</span></div>
    <div class="still-life" role="img" aria-label="Photograph of a white wine bottle, a filled wine glass and a bunch of green grapes"></div>
  </main>
</body>
</html>
```